Building company buisness cards

We are looking for a sharp modern new look for our business cards.
We are a New Zealand based company that specialises in house and land packages.
We have attached a photo of the current logo and would like to see if it can be improved somehow if needed.
We are open to any colours but we have chosen green at this stage.
Feel free to change the font and make the logo smarter looking.
Play with the colours and see what looks best.

We want a card that looks so good know one will want to throw it away!

Target Market(s)

Home buyers

Industry/Entity Type

Building

Contact Information for Business Card

Derek Tolvane
0217394062
dtolvane@quillmarkhomesteads.co.nz
quillmarkhomesteads.co.nz

Font styles to use
Serif
Sans Serif

Colors

Designer to choose colors to be used in the design.

Requirements
Must have
• Logo and company name on one side, details on the other side
Nice to have
• Color codes for the original green are HEX #4a8028, RGB(74,128,40), CMYK(42,0,69,50)
• Round corners, Raised and/or spot UV

```html
<!DOCTYPE html>
<html lang="en">
<head>
<meta charset="utf-8">
<title>Quillmark Homesteads — Business Card</title>
<link rel="stylesheet" href="https://fonts.googleapis.com/css2?family=Open+Sans:wght@300;400;700&family=Oswald:wght@500&display=swap">
<style>
  :root {
    --backdrop: #2b2b2b;
    --card: #232323;
    --ink-white: #f2f2f2;
    --ink-silver: #bdbdbd;
    --ink-soft: #d6d6d6;
    --brand-green: #4a8028;
    --edge-green: #3f8a2e;
  }
  * { margin: 0; padding: 0; box-sizing: border-box; }
  html, body {
    width: 1200px; height: 900px; overflow: hidden;
    background: var(--backdrop);
  }
  .canvas {
    position: relative; width: 1200px; height: 900px;
    display: flex; flex-direction: column; align-items: center; justify-content: center;
    gap: 40px;
  }
  .card {
    position: relative; width: 660px; height: 377px;
    background: var(--card);
    border-radius: 6px;
    box-shadow: 0 14px 30px rgba(0,0,0,0.45);
    overflow: hidden;
  }
  /* Front */
  .card-front { display: flex; align-items: center; justify-content: center; }
  .brand { text-align: center; }
  .brand-name {
    font-family: "Open Sans", sans-serif; font-weight: 700;
    font-size: 40px; letter-spacing: -0.5px; color: var(--ink-silver);
  }
  .brand-rule {
    width: 110px; height: 1px; margin: 10px auto 0;
    background: var(--ink-silver); opacity: 0.5;
  }
  /* Back */
  .card-back { display: flex; align-items: center; }
  .identity {
    width: 300px; text-align: right; padding-right: 16px;
  }
  .person-name {
    font-family: "Oswald", sans-serif; font-weight: 500;
    font-size: 38px; letter-spacing: 1.5px; line-height: 1.05;
    color: var(--ink-white); text-transform: uppercase;
  }
  .person-role {
    font-family: "Open Sans", sans-serif; font-weight: 400;
    font-size: 18px; letter-spacing: 0.5px; color: var(--brand-green);
    text-transform: uppercase; margin-top: 2px;
  }
  .divider { width: 2px; height: 78px; background: var(--ink-white); }
  .contacts { list-style: none; padding-left: 18px; }
  .contacts li {
    display: flex; align-items: center; gap: 12px;
    font-family: "Open Sans", sans-serif; font-weight: 300;
    font-size: 16px; color: var(--ink-soft); line-height: 26px;
  }
  .contacts svg { width: 14px; height: 14px; flex: none; }
  .accent { color: var(--brand-green); }
  .edge-line {
    position: absolute; left: 0; right: 0; bottom: 0; height: 5px;
    background: var(--edge-green);
  }
</style>
</head>
<body>
<main class="canvas">
  <section class="card card-front" aria-label="Card front">
    <div class="brand">
      <div class="brand-name">Quillmark Homesteads</div>
      <div class="brand-rule"></div>
    </div>
  </section>

  <section class="card card-back" aria-label="Card back">
    <div class="identity">
      <div class="person-name">Derek Tolvane</div>
      <div class="person-role">Owner</div>
    </div>
    <div class="divider"></div>
    <ul class="contacts">
      <li>
        <svg viewBox="0 0 14 14" aria-hidden="true"><rect x="3.5" y="1" width="7" height="12" rx="1.2" fill="none" stroke="#4a8028" stroke-width="1.5"/><circle cx="7" cy="11" r="0.8" fill="#4a8028"/></svg>
        0217394062
      </li>
      <li>
        <svg viewBox="0 0 14 14" aria-hidden="true"><rect x="1" y="3" width="12" height="8.5" rx="1" fill="#4a8028"/><path d="M1.5 3.6 7 8 12.5 3.6" fill="none" stroke="#232323" stroke-width="1.2"/></svg>
        dtolvane@quillmarkhomesteads.co.nz
      </li>
      <li>
        <svg viewBox="0 0 14 14" aria-hidden="true"><circle cx="8" cy="6" r="4" fill="none" stroke="#4a8028" stroke-width="1.6"/><line x1="5.2" y1="8.8" x2="1.5" y2="12.5" stroke="#4a8028" stroke-width="1.8" stroke-linecap="round"/></svg>
        <span>www.<span class="accent">quillmarkhomesteads</span>.co.nz</span>
      </li>
    </ul>
    <div class="edge-line"></div>
  </section>
</main>
</body>
</html>
```